Business Card Design

My business is writing crime novels to entertain readers. I write legal thrillers and mysteries. I need a card for publishers, agents, other authors, and media.

Industry/Entity Type

Legal

Contact Information for Business Card

Paul Derrow
www.derrowfiction.example
pauljderrow@inkpost.example
0064 27 5190472

```html
<!DOCTYPE html>
<html lang="en">
<head>
<meta charset="utf-8">
<title>Paul Derrow — Business Card</title>
<link rel="stylesheet" href="https://fonts.googleapis.com/css2?family=Cabin+Condensed:wght@500;600;700&display=swap">
<style>
  :root {
    --page-bg: #d9d6d2;
    --card-light: #ffffff;
    --card-edge: #e6e6e6;
    --tape-yellow: #f6e91a;
    --tape-ink: #0d0d0d;
    --contact-ink: #111111;
  }
  html, body {
    margin: 0;
    width: 1200px;
    height: 1181px;
    overflow: hidden;
    background: var(--page-bg);
  }
  .business-card {
    position: absolute;
    left: 80px;
    top: 291px;
    width: 1040px;
    height: 598px;
    box-shadow: 0 10px 30px rgba(0,0,0,0.25);
  }
  .business-card svg { display: block; width: 100%; height: 100%; }
  .tape-text {
    font-family: "Cabin Condensed", "Arial Narrow", sans-serif;
    font-weight: 700;
    font-size: 88px;
    fill: var(--tape-ink);
    text-anchor: middle;
    dominant-baseline: central;
  }
  .contact-line {
    font-family: "Cabin Condensed", "Gill Sans", sans-serif;
    font-weight: 500;
    font-size: 23px;
    fill: var(--contact-ink);
    text-anchor: middle;
  }
</style>
</head>
<body>
  <div class="business-card">
    <svg viewBox="0 0 863 496" xmlns="http://www.w3.org/2000/svg">
      <defs>
        <radialGradient id="card-surface" cx="50%" cy="40%" r="70%">
          <stop offset="0" stop-color="var(--card-light)"/>
          <stop offset="1" stop-color="var(--card-edge)"/>
        </radialGradient>
        <filter id="tape-shadow" x="-10%" y="-50%" width="120%" height="200%">
          <feDropShadow dx="0" dy="6" stdDeviation="5" flood-color="#000" flood-opacity="0.25"/>
        </filter>
        <clipPath id="card-clip"><rect width="863" height="496"/></clipPath>
      </defs>

      <rect class="card-surface" width="863" height="496" fill="url(#card-surface)"/>

      <g clip-path="url(#card-clip)">
        <g class="tape tape-crime-scene" transform="translate(431 250) rotate(17.6)" filter="url(#tape-shadow)">
          <rect x="-700" y="-44" width="1400" height="88" fill="var(--tape-yellow)"/>
          <text class="tape-text" x="-515" y="0">CRIME SCENE</text>
          <text class="tape-text" x="0" y="0">CRIME SCENE</text>
          <text class="tape-text" x="515" y="0">CRIME SCENE</text>
        </g>

        <g class="tape tape-name" transform="translate(431 250) rotate(-17.6)" filter="url(#tape-shadow)">
          <rect x="-700" y="-46" width="1400" height="92" fill="var(--tape-yellow)"/>
          <text class="tape-text" x="-610" y="0">PAUL DERROW</text>
          <text class="tape-text" x="0" y="0">PAUL DERROW</text>
          <text class="tape-text" x="610" y="0">PAUL DERROW</text>
        </g>
      </g>

      <g class="contact-details">
        <text class="contact-line" x="431" y="411">0064 27 5190472</text>
        <text class="contact-line" x="431" y="442">pauljderrow@inkpost.example</text>
        <text class="contact-line" x="431" y="472">www.derrowfiction.example</text>
      </g>
    </svg>
  </div>
</body>
</html>
```